Infografik/ Zeitleiste für Startup
Zielgruppe
Wir sind ein Startup, das über die Seite Kalendaro.de zukünftig folgenden Service anbietet: Unternehmer können sehr flexibel (selbst) gestaltete Terminformulare erstellen und auf Ihrer Website einbinden. Kunden können dann diese Termine buchen und bekommen dann Erinnerungs-Mails und SMS.
Zielgruppe: Dienstleister wie Fotografen, Friseure, Versicherungsvertreter, Masseure, Restaurants, Arztpraxen. Also alle, die darauf angewiesen sind, dass vereinbarte Termine eingehalten werden und die die Terminvereinbarung vereinfachen wollen. Also weniger per Telefon, mehr über die eigene Website.
Kalendaro ist mit PunktWahl.com (aktuell noch Top-und-Flop.com) verknüpft. Kunden, die einen Termin wünschen, sehen die Bewertungen vorheriger Kunden. Das stärkt das Vertrauen und erhöht die Termin-Zuverlässigkeit (Verbessert die No-Show-Rate). Damit sinken auch die Werbekosten je Kunden (geringere Kosten pro Conversion).
Kalendaro.de und PunktWahl.com (aktuell noch Top-und-Flop.com) wurde vom Team von Bilder-Atelier.de entwickelt. Dank Kalendaro und PunktWahl.com haben wir (das Team von Bilder-Atelier.de) folgende Vorteile:
- verbesserte Termin-Zuverlässigkeit (No-Show-Rate)
- mehr Kunden, mehr Shootings
- höherer Umsatz
- Zeitersparnis bei der Terminvereinbarung
- Senkungen der Werbekosten je Kunden (geringere Kosten pro Conversion)
Das ist der Grund, warum wir Kalendaro und PunktWahl nun auch für andere Branchen anbieten.
Siehe auch: https://www.videoplattform.example/watch?v=Qm7Rt2Lp9Xz
Siehe auch: https://www.videoplattform.example/watch?v=Vn4Kd8Sw3Hb
Aufgabenstellung
Wir benötigen für Kalendaro.de eine Infografik. Diese soll verdeutlichen, welche Vorteile wir (Bilder-Atelier.de) dank Kalendaro und PunktWahl haben:
Der Betrachter soll diese Zahlen auf einen Blick werten und die Vorteile für SEIN GESCHÄFT erkennen können. Zum Beispiel anhand einer Zeitleiste, die die Entwicklung der verschiedenen Kennzahlen wiedergibt.
Die Kennzahlen (die Entwicklung) können Sie hier aufrufen: https://ablage.example/ordner/7KpRwZ2mNc5Qx8LtVb3HyJ6dFs9GaE1Uo?usp=sharing
Besonders soll die positive Entwicklung ab Ende September 2017 deutlich werden. Ab Ende September 2017 haben wir Kalendaro und PunktWahl.com für die Terminvereinbarung genutzt. Vorher haben wir Termine per Email und Telefon vereinbart, was deutlich zeitintensiver war.
Das Design der Zeitleiste (der Infografik) soll sich an Kalendaro.de orientieren.
Falls die sechs Kennzahlen nicht übersichtlich in einer Zeitleiste darstellbar sind, könnten die Kennzahlen auf mehrere Grafiken aufgeteilt werden.
Vorstellbar ist auch eine interaktive Infografik, bei der man die jeweilige Kennzahl auswählen kann.
Wir lassen uns hier gerne von Ihrer Kreativität überraschen. Der spätere Kunde/Nutzer/ Betrachter der Infografik steht bitte im Vordergrund jeder Überlegung/jedes Designs.
Nutzen Sie ggf. bitte Icons und verschiedenen Farben, um die verschiedenen Kennzahlen auch visuell zu verdeutlichen.
Die Infografik soll später auf https://developer.kalendaro.de/de/about-us.html und in Flyern veröffentlicht werden.
Wesentliche Funktionen und Vorteile siehe auch:
https://www.videoplattform.example/watch?v=Qm7Rt2Lp9Xz
https://www.videoplattform.example/watch?v=Vn4Kd8Sw3Hb
Die einzelnen gr..

```html
<!DOCTYPE html>
<html lang="de">
<head>
<meta charset="utf-8">
<title>Kalendaro – Kennzahlen im Überblick</title>
<link rel="stylesheet" href="https://fonts.googleapis.com/css2?family=Ubuntu:wght@300;400;500;700&display=swap">
<style>
  :root {
    --red: #e30613;
    --green: #86b626;
    --yellow: #fdc900;
    --bar: #84939c;
    --text-grey: #6e767c;
    --subtitle: #70787e;
    --white: #ffffff;
  }
  html, body {
    margin: 0;
    padding: 0;
    width: 1200px;
    height: 563px;
    overflow: hidden;
    background: var(--white);
    font-family: "Ubuntu", sans-serif;
  }
  .canvas { position: relative; width: 1200px; height: 563px; }
  .icon-library { position: absolute; width: 0; height: 0; }
  .panel { position: absolute; width: 325px; }
  .panel--shootings  { left: 44px;  top: 50px; }
  .panel--kunden     { left: 428px; top: 50px; }
  .panel--umsatz     { left: 821px; top: 50px; }
  .panel--zeit       { left: 44px;  top: 300px; }
  .panel--werbung    { left: 428px; top: 300px; }
  .panel--noshow     { left: 821px; top: 300px; }
  .tab {
    height: 16px;
    line-height: 16px;
    width: 140px;
    color: var(--white);
    font-weight: 700;
    font-size: 11.5px;
    letter-spacing: 1.1px;
    text-align: center;
  }
  .tab--narrow { width: 122px; }
  .tab--red { background: var(--red); }
  .tab--green { background: var(--green); }
  .tab--yellow { background: var(--yellow); }
  .chart { display: block; width: 325px; height: 192px; overflow: hidden; }
  .subtitle { font-size: 10.5px; fill: var(--subtitle); }
  .value { font-size: 16px; fill: var(--text-grey); font-weight: 300; text-anchor: middle; }
  .basis { font-size: 8px; fill: var(--text-grey); text-anchor: middle; }
  .change { font-size: 23px; font-weight: 700; letter-spacing: 1px; }
  .change .sign { font-weight: 400; }
  .change--red { fill: var(--red); }
  .change--green { fill: var(--green); }
  .change--yellow { fill: var(--yellow); }
  .axis-label { font-size: 8px; fill: var(--white); text-anchor: middle; font-weight: 500; }
  .tick { stroke: #a9b2b8; stroke-width: 0.8; }
</style>
</head>
<body>
<div class="canvas">

  <svg class="icon-library" aria-hidden="true">
    <defs>
      <linearGradient id="section-before" x1="0" y1="0" x2="1" y2="1">
        <stop offset="0" stop-color="#c2c9cf"/>
        <stop offset="1" stop-color="#d9dee2"/>
      </linearGradient>
      <linearGradient id="section-after" x1="0" y1="0" x2="1" y2="0">
        <stop offset="0" stop-color="#b4bfc7"/>
        <stop offset="1" stop-color="#fbfbfc"/>
      </linearGradient>
      <linearGradient id="beam-grow" x1="0" y1="0" x2="1" y2="0">
        <stop offset="0" stop-color="#ffffff" stop-opacity="0.15"/>
        <stop offset="1" stop-color="#ffffff" stop-opacity="0.95"/>
      </linearGradient>
      <linearGradient id="beam-shrink" x1="0" y1="0" x2="1" y2="0">
        <stop offset="0" stop-color="#ffffff" stop-opacity="0.2"/>
        <stop offset="1" stop-color="#ffffff" stop-opacity="0.95"/>
      </linearGradient>

      <symbol id="icon-aperture" viewBox="-50 -50 100 100">
        <circle r="48" fill="var(--red)"/>
        <g fill="none" stroke="#fff" stroke-width="5" stroke-linecap="round">
          <path id="blade" d="M -12 -42 Q 18 -30 22 4"/>
          <use href="#blade" transform="rotate(60)"/>
          <use href="#blade" transform="rotate(120)"/>
          <use href="#blade" transform="rotate(180)"/>
          <use href="#blade" transform="rotate(240)"/>
          <use href="#blade" transform="rotate(300)"/>
        </g>
      </symbol>

      <symbol id="icon-coin" viewBox="-50 -50 100 100">
        <circle r="48" fill="var(--yellow)"/>
        <circle r="36" fill="none" stroke="#fff" stroke-width="6"/>
        <text x="-1" y="17" text-anchor="middle" font-family="Ubuntu, sans-serif" font-weight="700" font-size="50" fill="#fff">€</text>
      </symbol>

      <symbol id="icon-stopwatch" viewBox="-50 -50 100 100">
        <rect x="-10" y="-50" width="20" height="9" rx="2" fill="var(--green)"/>
        <rect x="-4" y="-43" width="8" height="8" fill="var(--green)"/>
        <rect x="-45" y="-38" width="12" height="9" rx="2" fill="var(--green)" transform="rotate(-45 -39 -33)"/>
        <rect x="33" y="-38" width="12" height="9" rx="2" fill="var(--green)" transform="rotate(45 39 -33)"/>
        <circle cy="8" r="42" fill="var(--green)"/>
        <circle cy="8" r="32" fill="var(--green)" stroke="#fff" stroke-width="5"/>
        <path d="M 0 8 L 0 -18 A 26 26 0 0 1 18 -10 Z" fill="#a3c95a"/>
      </symbol>

      <symbol id="icon-megaphone" viewBox="-50 -50 100 100">
        <circle r="48" fill="var(--yellow)"/>
        <g fill="#fff">
          <rect x="-34" y="-8" width="6" height="16"/>
          <polygon points="-26,-9 10,-26 10,24 -26,8"/>
          <polygon points="-22,8 -12,8 -18,28 -28,28"/>
          <rect x="16" y="-18" width="14" height="7"/>
          <rect x="16" y="-4" width="14" height="7"/>
          <rect x="16" y="10" width="14" height="7"/>
        </g>
      </symbol>

      <symbol id="icon-seat" viewBox="-50 -50 100 100">
        <circle r="48" fill="var(--red)"/>
        <g fill="#fff">
          <rect x="-18" y="-32" width="36" height="32" rx="5"/>
          <rect x="-30" y="-6" width="10" height="24" rx="3"/>
          <rect x="20" y="-6" width="10" height="24" rx="3"/>
          <rect x="-24" y="6" width="48" height="12"/>
          <rect x="-22" y="18" width="4" height="12"/>
          <rect x="18" y="18" width="4" height="12"/>
        </g>
        <g fill="var(--red)">
          <rect x="-10" y="-26" width="4" height="18"/>
          <rect x="-2" y="-26" width="4" height="18"/>
          <rect x="6" y="-26" width="4" height="18"/>
        </g>
      </symbol>

      <symbol id="icon-customer" viewBox="-50 -50 100 100">
        <circle r="48" fill="var(--green)"/>
      </symbol>
    </defs>
  </svg>

  <!-- Shootings -->
  <section class="panel panel--shootings">
    <div class="tab tab--red">SHOOTINGS</div>
    <svg class="chart" viewBox="0 0 325 192">
      <rect x="0" y="0" width="141" height="179" fill="url(#section-before)"/>
      <rect x="141" y="0" width="184" height="179" fill="url(#section-after)"/>
      <line x1="141" y1="0" x2="141" y2="179" stroke="#fff" stroke-width="1"/>
      <polygon points="55,72 300,47 300,127 55,102" fill="url(#beam-grow)"/>
      <text class="subtitle" x="148" y="18" textLength="168" lengthAdjust="spacingAndGlyphs">Nutzung Kalendaro und PunktWahl</text>
      <use href="#icon-aperture" x="41" y="73" width="28" height="28"/>
      <use href="#icon-aperture" x="238" y="47" width="80" height="80"/>
      <text class="change change--red" x="150" y="96"><tspan class="sign">+ </tspan>XX <tspan class="sign">%</tspan></text>
      <text class="value" x="55" y="124">9</text>
      <text class="value" x="278" y="148">25</text>
      <line class="tick" x1="55" y1="171" x2="55" y2="179"/>
      <line class="tick" x1="278" y1="171" x2="278" y2="179"/>
      <rect x="0" y="179" width="325" height="13" fill="var(--bar)"/>
      <text class="axis-label" x="54" y="189">MAI 17</text>
      <text class="axis-label" x="142" y="189">OKT 17</text>
      <text class="axis-label" x="278" y="189">SEP 18</text>
    </svg>
  </section>

  <!-- Kunden -->
  <section class="panel panel--kunden">
    <div class="tab tab--green">KUNDEN</div>
    <svg class="chart" viewBox="0 0 326 192">
      <rect x="0" y="0" width="142" height="179" fill="url(#section-before)"/>
      <rect x="142" y="0" width="184" height="179" fill="url(#section-after)"/>
      <line x1="142" y1="0" x2="142" y2="179" stroke="#fff" stroke-width="1"/>
      <polygon points="57,70 300,46 300,128 57,100" fill="url(#beam-grow)"/>
      <text class="subtitle" x="148" y="18" textLength="168" lengthAdjust="spacingAndGlyphs">Nutzung Kalendaro und PunktWahl</text>
      <use href="#icon-customer" x="43" y="71" width="28" height="28" role="img" aria-label="Kundensymbol, klein"/>
      <use href="#icon-customer" x="240" y="45" width="84" height="84" role="img" aria-label="Kundensymbol, groß"/>
      <text class="change change--green" x="150" y="96"><tspan class="sign">+ </tspan>XX <tspan class="sign">%</tspan></text>
      <text class="value" x="57" y="124">144</text>
      <text class="value" x="280" y="148">425</text>
      <line class="tick" x1="57" y1="171" x2="57" y2="179"/>
      <line class="tick" x1="281" y1="171" x2="281" y2="179"/>
      <rect x="0" y="179" width="326" height="13" fill="var(--bar)"/>
      <text class="axis-label" x="55" y="189">MAI 17</text>
      <text class="axis-label" x="143" y="189">OKT 17</text>
      <text class="axis-label" x="280" y="189">SEP 18</text>
    </svg>
  </section>

  <!-- Umsatz -->
  <section class="panel panel--umsatz">
    <div class="tab tab--yellow">UMSATZ</div>
    <svg class="chart" viewBox="0 0 325 192">
      <rect x="0" y="0" width="140" height="179" fill="url(#section-before)"/>
      <rect x="140" y="0" width="185" height="179" fill="url(#section-after)"/>
      <line x1="140" y1="0" x2="140" y2="179" stroke="#fff" stroke-width="1"/>
      <polygon points="55,66 300,47 300,127 55,108" fill="url(#beam-grow)"/>
      <text class="subtitle" x="146" y="18" textLength="168" lengthAdjust="spacingAndGlyphs">Nutzung Kalendaro und PunktWahl</text>
      <use href="#icon-coin" x="32" y="64" width="46" height="46"/>
      <use href="#icon-coin" x="238" y="47" width="80" height="80"/>
      <text class="change change--yellow" x="150" y="96"><tspan class="sign">+ </tspan>74 <tspan class="sign">%</tspan></text>
      <text class="value" x="55" y="136">100</text>
      <text class="basis" x="55" y="146">(Basis)</text>
      <text class="value" x="278" y="150">174</text>
      <line class="tick" x1="55" y1="171" x2="55" y2="179"/>
      <line class="tick" x1="278" y1="171" x2="278" y2="179"/>
      <rect x="0" y="179" width="325" height="13" fill="var(--bar)"/>
      <text class="axis-label" x="53" y="189">MAI 17</text>
      <text class="axis-label" x="141" y="189">OKT 17</text>
      <text class="axis-label" x="278" y="189">SEP 18</text>
    </svg>
  </section>

  <!-- Zeitaufwand -->
  <section class="panel panel--zeit">
    <div class="tab tab--green">ZEITAUFWAND</div>
    <svg class="chart" viewBox="0 0 325 192">
      <rect x="0" y="0" width="141" height="179" fill="url(#section-before)"/>
      <rect x="141" y="0" width="184" height="179" fill="url(#section-after)"/>
      <line x1="141" y1="0" x2="141" y2="179" stroke="#fff" stroke-width="1"/>
      <polygon points="55,52 292,78 292,98 55,124" fill="url(#beam-shrink)"/>
      <text class="subtitle" x="148" y="18" textLength="168" lengthAdjust="spacingAndGlyphs">Nutzung Kalendaro und PunktWahl</text>
      <use href="#icon-stopwatch" x="13" y="38" width="84" height="84"/>
      <use href="#icon-stopwatch" x="268" y="77" width="20" height="20"/>
      <text class="change change--green" x="150" y="96"><tspan class="sign">- </tspan>XX <tspan class="sign">%</tspan></text>
      <text class="value" x="55" y="150">61</text>
      <text class="value" x="278" y="147">13</text>
      <line class="tick" x1="55" y1="171" x2="55" y2="179"/>
      <line class="tick" x1="278" y1="171" x2="278" y2="179"/>
      <rect x="0" y="179" width="325" height="13" fill="var(--bar)"/>
      <text class="axis-label" x="54" y="189">MAI 17</text>
      <text class="axis-label" x="142" y="189">OKT 17</text>
      <text class="axis-label" x="278" y="189">SEP 18</text>
    </svg>
  </section>

  <!-- Werbekosten -->
  <section class="panel panel--werbung">
    <div class="tab tab--yellow">WERBEKOSTEN</div>
    <svg class="chart" viewBox="0 0 326 192">
      <rect x="0" y="0" width="142" height="179" fill="url(#section-before)"/>
      <rect x="142" y="0" width="184" height="179" fill="url(#section-after)"/>
      <line x1="142" y1="0" x2="142" y2="179" stroke="#fff" stroke-width="1"/>
      <polygon points="60,48 300,60 300,112 60,124" fill="url(#beam-shrink)"/>
      <text class="subtitle" x="148" y="18" textLength="168" lengthAdjust="spacingAndGlyphs">Nutzung Kalendaro und PunktWahl</text>
      <use href="#icon-megaphone" x="22" y="48" width="76" height="76"/>
      <use href="#icon-megaphone" x="256" y="60" width="52" height="52"/>
      <text class="change change--yellow" x="155" y="96"><tspan class="sign">- </tspan>33 <tspan class="sign">%</tspan></text>
      <text class="value" x="57" y="142">100</text>
      <text class="basis" x="57" y="152">(Basis)</text>
      <text class="value" x="280" y="147">67</text>
      <line class="tick" x1="57" y1="171" x2="57" y2="179"/>
      <line class="tick" x1="281" y1="171" x2="281" y2="179"/>
      <rect x="0" y="179" width="326" height="13" fill="var(--bar)"/>
      <text class="axis-label" x="55" y="189">MAI 17</text>
      <text class="axis-label" x="143" y="189">OKT 17</text>
      <text class="axis-label" x="280" y="189">SEP 18</text>
    </svg>
  </section>

  <!-- No-Show-Rate -->
  <section class="panel panel--noshow">
    <div class="tab tab--red tab--narrow">NO-SHOW-RATE</div>
    <svg class="chart" viewBox="0 0 325 192">
      <rect x="0" y="0" width="140" height="179" fill="url(#section-before)"/>
      <rect x="140" y="0" width="185" height="179" fill="url(#section-after)"/>
      <line x1="140" y1="0" x2="140" y2="179" stroke="#fff" stroke-width="1"/>
      <polygon points="55,52 290,72 290,100 55,120" fill="url(#beam-shrink)"/>
      <text class="subtitle" x="146" y="18" textLength="168" lengthAdjust="spacingAndGlyphs">Nutzung Kalendaro und PunktWahl</text>
      <use href="#icon-seat" x="20" y="51" width="70" height="70"/>
      <use href="#icon-seat" x="262" y="72" width="28" height="28"/>
      <text class="change change--red" x="150" y="96"><tspan class="sign">- </tspan>XX <tspan class="sign">%</tspan></text>
      <text class="value" x="55" y="144">9</text>
      <text class="value" x="276" y="147">25</text>
      <line class="tick" x1="55" y1="171" x2="55" y2="179"/>
      <line class="tick" x1="278" y1="171" x2="278" y2="179"/>
      <rect x="0" y="179" width="325" height="13" fill="var(--bar)"/>
      <text class="axis-label" x="53" y="189">MAI 17</text>
      <text class="axis-label" x="141" y="189">OKT 17</text>
      <text class="axis-label" x="278" y="189">SEP 18</text>
    </svg>
  </section>

</div>
</body>
</html>
```